Postcard Design

We are a High intensity gym in need of a postcard that shows a possible picture of one of our coaches coaching. Corvane’s mission is to bring high intensity, results-oriented workouts to the heart of Baltimore’s Inner Harbor. This is more than just a gym – our goal is to inspire, educate, and bring fun, functional workouts to everyone! IIt doesn't have to say all of that but it does need our information and where to find us. Plus, an offer for 2 weeks free if they text the word "Perform" to 41382. Which should be the main focal point.And our website and facebook info.

Target Market(s)

Fitness, women and men ages 20-60

Industry/Entity Type

Gym

Requirements
Must have
• REMOVE DYNAVOLT FROM THE TOP OF MY LOGO

```html
<!DOCTYPE html>
<html lang="en">
<head>
<meta charset="utf-8">
<title>Corvane Performance Center Postcard</title>
<link rel="stylesheet" href="https://fonts.googleapis.com/css2?family=Bebas+Neue&family=Raleway:wght@300;400;600&family=Mulish:wght@400&display=swap">
<style>
  :root {
    --paper: #ffffff;
    --ink: #1a1a1a;
    --dark: #141414;
    --photo-light: #a6a49d;
    --photo-mid: #6b6963;
    --photo-warm: #7a7161;
    --photo-deep: #1f1f1e;
    --accent: #f5e61a;
    --white: #ffffff;
    --rule: #d9d9d9;
    --stamp-line: #cfcfcf;
  }
  * { margin: 0; padding: 0; box-sizing: border-box; }
  html, body { width: 1200px; height: 930px; overflow: hidden; background: var(--paper); }
  .canvas { position: relative; width: 1200px; height: 930px; }

  .front {
    position: absolute; left: 0; top: 0; width: 580px; height: 765px;
    background: var(--dark); overflow: hidden;
  }
  .front__photo {
    position: absolute; left: 0; top: 0; width: 580px; height: 765px;
    background:
      radial-gradient(ellipse 38% 55% at 8% 50%, rgba(150,148,142,0.75) 0%, rgba(150,148,142,0) 100%),
      radial-gradient(ellipse 30% 40% at 40% 42%, rgba(122,113,97,0.7) 0%, rgba(122,113,97,0) 100%),
      radial-gradient(ellipse 60% 35% at 50% 32%, var(--photo-light) 0%, var(--photo-mid) 55%, rgba(40,40,38,0.2) 100%),
      linear-gradient(180deg, #2a2a28 0%, var(--photo-mid) 30%, #4a4844 62%, var(--photo-deep) 100%);
  }
  .front__art { position: absolute; left: 0; top: 0; width: 580px; height: 765px; }

  .offer {
    position: absolute; left: 140px; top: 44px;
    font-family: "Raleway", sans-serif; font-weight: 300;
    color: var(--white); font-size: 36px; line-height: 46px; white-space: nowrap;
  }
  .offer__keyword { color: var(--accent); font-weight: 600; }
  .offer__number { color: var(--white); font-weight: 600; }
  .offer__highlight, .offer__free {
    font-family: "Bebas Neue", sans-serif; font-size: 54px; letter-spacing: 0.5px;
  }
  .offer__highlight { color: var(--accent); }
  .offer__free { color: var(--white); }

  .values {
    position: absolute; right: 23px; top: 302px; text-align: right;
    font-family: "Bebas Neue", sans-serif; font-size: 90px; line-height: 79px;
    letter-spacing: -1px; list-style: none;
  }
  .values__item--white { color: var(--white); }
  .values__item--yellow { color: var(--accent); }

  .phone {
    position: absolute; right: 22px; top: 684px;
    font-family: "Bebas Neue", sans-serif; font-size: 70px; line-height: 70px;
    color: var(--white); letter-spacing: 1px;
  }

  .back__address {
    position: absolute; left: 575px; top: 96px; width: 335px; text-align: center;
    font-family: "Mulish", sans-serif; font-size: 19px; line-height: 41px; color: var(--ink);
    font-style: normal;
  }
  .back__online {
    position: absolute; left: 575px; top: 240px; width: 335px; text-align: center;
    font-family: "Mulish", sans-serif; font-size: 16px; line-height: 28px; color: var(--ink);
  }
  .back__stamp {
    position: absolute; left: 903px; top: 27px; width: 265px; height: 266px;
    border: 2px solid var(--stamp-line);
  }
  .back__rule {
    position: absolute; left: 640px; width: 497px; height: 3px; background: var(--rule);
  }
</style>
</head>
<body>
<main class="canvas">
  <section class="front">
    <div class="front__photo" role="img" aria-label="Photo of a coach leading a group class of athletes holding training poles in the gym"></div>
    <svg class="front__art" width="580" height="765" viewBox="0 0 580 765" aria-hidden="true">
      <rect x="0" y="0" width="580" height="145" fill="#141414" opacity="0.82"/>
      <polygon points="0,52 100,52 128,145 0,145" fill="#8a8a8a" opacity="0.45"/>
      <polygon points="0,716 93,716 110,665 580,665 580,765 0,765" fill="#000" opacity="0.45"/>
      <polyline points="0,713 95,713 112,662 580,662" fill="none" stroke="#f5e61a" stroke-width="4"/>
    </svg>
    <p class="offer">
      text <span class="offer__keyword">"Perform"</span> to <span class="offer__number">41382</span><br>
      get <span class="offer__highlight">2 Weeks</span> <span class="offer__free">Free Trial</span>
    </p>
    <ul class="values">
      <li class="values__item--white">Fun</li>
      <li class="values__item--yellow">Workout</li>
      <li class="values__item--white">Education</li>
      <li class="values__item--yellow">Inspiration</li>
    </ul>
    <p class="phone">717-555-0182</p>
  </section>

  <section class="back">
    <address class="back__address">
      Corvane Performance Center<br>
      418 E. Harbor St. Suite 200<br>
      Baltimore, MD. 21230
    </address>
    <p class="back__online">
      corvaneperformance.com<br>
      Follow us: @corvaneperformance
    </p>
    <div class="back__stamp"></div>
    <div class="back__rule" style="top:416px"></div>
    <div class="back__rule" style="top:500px"></div>
    <div class="back__rule" style="top:584px"></div>
    <div class="back__rule" style="top:666px"></div>
  </section>
</main>
</body>
</html>
```